Bright Harbor, LLC Business Card Design

We need a product business card designed for a new company Bright Harbor, LLC. We make and resell waterless RV cleaner, polish and protectant. It cleans and protects in a simple spray and wipe step leaving the surface protected and conditioned to repel dust, dirt, water, smudges, bugs and fingerprints while preventing fogging. Safe on acrylic, plexiglas, lexan, plastic, rubber, painted surfaces, chrome, stainless, aluminum, vinyl, leather, glass.... This is an eco-friendly green product.

We want to play off the company name to tell the consumer that the product is easy to use and associate to the nostalgics 1950's in the USA... Thinking old travel trailer with hot rod truck pulling it as the graphic, maybe the husband cleaning the truck and the wife cleaning the trailer for a Bright Harbor surface.
Updates

Just posted our newly finished logo. Need to have "Cleaner and Protectant" added to the design as well. Thanks everyone that has submitted thus far, i am working to get comments on all.

If you need a different file format, please let me know. Thank you.

Most important info, is the logo, website and the words "Cleaner" or "Clean" along "Protectant" or "Protect" the remainder is of less importance. Highlight: www.brightharborwash.example Focus is on company brand for Brighter Harbor Cleaner product: However, need a section for the following contact info: Walt Ferris (xxx) xxx-xxxx email address Would like space for QR Code if possible.

Target Market(s)

Adults in the USA between ages of 35-75 that are actively involved in the Recreational Vehicle (RV), travel trailer, and hot rod lifestyle. We are targeting the RV marked of the high end travel, 5th wheel and bus RV market. Along with hot rods, automotive and motorcycle market.

Industry/Entity Type

Travel

Requirements
Must have
• Most important info, is the logo, website and the words "Cleaner" or "Clean" along "Protectant" or "Protect" the remainder is of less importance.

Highlight:
www.brightharborwash.example

Focus is on company brand for Brighter Harbor Cleaner product: However, need a section for the following contact info:

Walt Ferris
(xxx) xxx-xxxx
email address
Nice to have
• Would like a space for a QR Code.

```html
<!DOCTYPE html>
<html lang="en">
<head>
<meta charset="utf-8">
<title>Bright Harbor, LLC — Business Card</title>
<link href="https://fonts.googleapis.com/css2?family=Arimo:wght@400&family=Open+Sans:wght@400;700&display=swap" rel="stylesheet">
<style>
  :root {
    --canvas: #e6e6e6;
    --card-white: #ffffff;
    --panel-black: #141414;
    --frame-dark: #1c1c1c;
    --illustration-top: #3a3a3a;
    --illustration-bottom: #101010;
    --brand-blue: #1f78c8;
    --ink: #2a2a2a;
    --muted-ink: #3c3c3c;
    --paper: #f7f7f7;
  }
  * { box-sizing: border-box; margin: 0; padding: 0; }
  html, body { width: 1200px; height: 800px; overflow: hidden; }
  body {
    background: var(--canvas);
    display: flex;
    align-items: center;
    justify-content: center;
    gap: 30px;
  }
  .card {
    width: 525px;
    height: 300px;
    position: relative;
    box-shadow: 0 6px 18px rgba(0,0,0,0.18);
  }

  /* Front */
  .card--front { background: var(--card-white); padding: 20px; }
  .front-panel {
    width: 100%;
    height: 100%;
    background: var(--panel-black);
    position: relative;
    overflow: hidden;
  }
  .front-illustration {
    position: absolute;
    left: 70px;
    top: 22px;
    width: 340px;
    height: 160px;
    border-radius: 6px;
    background: linear-gradient(180deg, var(--illustration-top), var(--illustration-bottom));
  }
  .front-brand {
    position: absolute;
    right: 24px;
    bottom: 22px;
    font-family: "Arimo", Arial, sans-serif;
    font-weight: 400;
    font-size: 44px;
    color: var(--card-white);
    letter-spacing: -0.5px;
    white-space: nowrap;
  }

  /* Back */
  .card--back { background: var(--frame-dark); padding: 22px; }
  .back-panel {
    width: 100%;
    height: 100%;
    background: var(--paper);
    padding: 20px 36px;
  }
  .back-brand {
    font-family: "Arimo", Arial, sans-serif;
    font-size: 34px;
    color: var(--brand-blue);
    letter-spacing: -0.5px;
    line-height: 1;
    margin-bottom: 4px;
    white-space: nowrap;
  }
  .back-tagline {
    font-family: "Open Sans", Arial, sans-serif;
    font-size: 12px;
    line-height: 1.3;
    color: var(--muted-ink);
    margin-bottom: 8px;
  }
  .contact-name {
    font-family: "Open Sans", Arial, sans-serif;
    font-weight: 700;
    font-size: 15px;
    color: var(--ink);
    line-height: 1.2;
  }
  .contact-role {
    font-family: "Open Sans", Arial, sans-serif;
    font-size: 12px;
    line-height: 1.25;
    color: var(--brand-blue);
    margin-bottom: 8px;
  }
  .contact-list { list-style: none; }
  .contact-list li {
    display: flex;
    align-items: center;
    gap: 12px;
    font-family: "Open Sans", Arial, sans-serif;
    font-size: 12.5px;
    color: var(--muted-ink);
    height: 21px;
    white-space: nowrap;
  }
  .contact-list .contact-website { font-weight: 700; color: var(--brand-blue); }
  .contact-icon { width: 12px; height: 12px; flex: none; fill: var(--brand-blue); }
</style>
</head>
<body>
  <section class="card card--front">
    <div class="front-panel">
      <div class="front-illustration" role="img" aria-label="Line drawing of a pickup truck in white on black"></div>
      <div class="front-brand">Bright Harbor, LLC</div>
    </div>
  </section>

  <section class="card card--back">
    <div class="back-panel">
      <div class="back-brand">Bright Harbor, LLC</div>
      <div class="back-tagline">Cleaner and Protectant</div>
      <div class="contact-name">Walt Ferris</div>
      <div class="contact-role">Manager</div>
      <ul class="contact-list">
        <li>
          <svg class="contact-icon" viewBox="0 0 24 24" aria-hidden="true"><path d="M6.6 10.8a15.1 15.1 0 0 0 6.6 6.6l2.2-2.2c.3-.3.7-.4 1-.2 1.1.4 2.3.6 3.6.6.6 0 1 .4 1 1V20c0 .6-.4 1-1 1A17 17 0 0 1 3 4c0-.6.4-1 1-1h3.5c.6 0 1 .4 1 1 0 1.3.2 2.5.6 3.6.1.3 0 .7-.2 1z"/></svg>
          555-014-2230
        </li>
        <li>
          <svg class="contact-icon" viewBox="0 0 24 24" aria-hidden="true"><path d="M6.6 10.8a15.1 15.1 0 0 0 6.6 6.6l2.2-2.2c.3-.3.7-.4 1-.2 1.1.4 2.3.6 3.6.6.6 0 1 .4 1 1V20c0 .6-.4 1-1 1A17 17 0 0 1 3 4c0-.6.4-1 1-1h3.5c.6 0 1 .4 1 1 0 1.3.2 2.5.6 3.6.1.3 0 .7-.2 1z"/></svg>
          555-014-2231
        </li>
        <li>
          <svg class="contact-icon" viewBox="0 0 24 24" aria-hidden="true"><path d="M2 6.5V19h20V6.5l-10 7.5z"/><path d="M2.5 5h19L12 12.3z"/></svg>
          hello@brightharborwash.example
        </li>
        <li>
          <svg class="contact-icon" viewBox="0 0 24 24" aria-hidden="true"><path d="M12 2a7 7 0 0 0-7 7c0 5.2 7 13 7 13s7-7.8 7-13a7 7 0 0 0-7-7zm0 9.5A2.5 2.5 0 1 1 12 6.5a2.5 2.5 0 0 1 0 5z"/></svg>
          4820 Juniper Lane Fairview, CA 90210
        </li>
        <li class="contact-website">
          <svg class="contact-icon" viewBox="0 0 24 24" aria-hidden="true"><path d="M12 2a10 10 0 1 0 0 20 10 10 0 0 0 0-20zm0 2c.9 0 2.2 1.8 2.8 5H9.2C9.8 5.8 11.1 4 12 4zM4.3 11h4.6a22 22 0 0 0 0 2H4.3a8 8 0 0 1 0-2zm.8 4h4.1c.3 1.6.8 3 1.4 4A8 8 0 0 1 5.1 15zm0-6a8 8 0 0 1 5.5-4c-.6 1-1.1 2.4-1.4 4zm6.9 11c-.9 0-2.2-1.8-2.8-5h5.6c-.6 3.2-1.9 5-2.8 5zm-1.1-7a20 20 0 0 1 0-2h2.2a20 20 0 0 1 0 2zm3.5 6c.6-1 1.1-2.4 1.4-4h4.1a8 8 0 0 1-5.5 4zm1.7-6a22 22 0 0 0 0-2h4.6a8 8 0 0 1 0 2zm-.3-4c-.3-1.6-.8-3-1.4-4a8 8 0 0 1 5.5 4z"/></svg>
          www.brightharborwash.example
        </li>
      </ul>
    </div>
  </section>
</body>
</html>
```